I would like some help creating my first business cards for my new business, I am a facilitator of a course that I have created. I am currently starting the sales promotion and marketing part of my business and need some help designing the business cards. Something fairly simple would be good, the core theme of my work is in connection of women to themselves and to each other. My initial design is a tree lit up by lights, a very mother earth type of image. This is not my design however so I probably am not legally able to use the design. I don't have a logo. Could you possibly assist with this?

I would really like to have the following details on the business card:
Meg Donlan
0431 582 917
hi.meg.donlan@larkmail.example

And also the image

Target Market(s)

Women who are living in an isolated environment

Industry/Entity Type

Counsellor

Contact Information for Business Card

Meg Donlan
Facilitator
hi.meg.donlan@larkmail.example
0431 582 917

Font styles to use
Other font styles liked:
• Handwriting - Dakota

Colors
e34197
fee18a
3276b5
33a6d7
33b8a4

Requirements
Must have
• 1) My details as above
• 2) a design (picture) that represents the mother earth theme similar to the designs included in the brief
• 3) no copyright attached to the design
• 4) Colours are very important but it is difficult to describe the colour using the colour wheel. Please refer to the example of the tree that I have included in the drop box.
• 5) I must apologise that I forgot to add the business card needs to have the name of the business in gold letters please: Riverbend Circle Gatherings Collective, thank you
Nice to have
• It would be great to use the tree design that I included in the brief, this is my favourite picture but I think it is probably copyrighted. If it's not, that is the one I would like on my business cards please.

```html
<!DOCTYPE html>
<html lang="en">
<head>
<meta charset="utf-8">
<title>Meg Donlan — Business Card</title>
<link href="https://fonts.googleapis.com/css2?family=Kalam:wght@400;700&family=Open+Sans:wght@400;700&display=swap" rel="stylesheet">
<style>
  :root {
    --backdrop: #d9d8c2;
    --card: #e8e6b8;
    --card-light: #eeecc6;
    --bark: #5a4630;
    --orange: #f7881f;
    --gold: #a87a12;
    --ink: #3e3a2e;
    --grey: #6f6c60;
    --leaf-teal: #9ccfc4;
    --leaf-peach: #f2c08d;
  }
  html, body {
    margin: 0;
    padding: 0;
    width: 1200px;
    height: 898px;
    overflow: hidden;
    background: var(--backdrop);
  }
  .card {
    position: absolute;
    left: 75px;
    top: 149px;
    width: 1050px;
    height: 600px;
    background:
      repeating-linear-gradient(90deg, rgba(255,255,255,0.07) 0 2px, rgba(0,0,0,0.025) 2px 5px),
      linear-gradient(160deg, var(--card-light), var(--card));
    box-shadow: 0 12px 30px rgba(60,55,30,0.25);
    overflow: hidden;
    font-family: "Open Sans", sans-serif;
  }
  .tree-illustration {
    position: absolute;
    left: 50px;
    top: 90px;
    width: 520px;
    height: 488px;
    border-radius: 48% 48% 8% 8%;
    background: radial-gradient(ellipse at 50% 40%, var(--leaf-peach) 0%, var(--leaf-teal) 45%, rgba(232,230,184,0) 72%),
                linear-gradient(180deg, rgba(90,70,48,0) 60%, rgba(90,70,48,0.35) 100%);
    opacity: 0.8;
  }
  .identity {
    position: absolute;
    right: 190px;
    top: 28px;
    text-align: right;
  }
  .identity .name {
    color: var(--orange);
    font-weight: 700;
    font-size: 30px;
    line-height: 1.1;
  }
  .identity .role {
    color: var(--grey);
    font-size: 20px;
    line-height: 1.1;
  }
  .business-name {
    position: absolute;
    left: 610px;
    top: 140px;
    width: 420px;
    margin: 0;
    font-family: "Kalam", cursive;
    font-weight: 700;
    font-size: 50px;
    line-height: 1.15;
    color: var(--gold);
    text-align: center;
  }
  .contact {
    position: absolute;
    left: 620px;
    top: 410px;
    list-style: none;
    margin: 0;
    padding: 0;
    color: var(--ink);
    font-size: 21px;
  }
  .contact li {
    display: flex;
    align-items: center;
    gap: 12px;
    margin-bottom: 10px;
  }
  .contact svg { width: 24px; height: 24px; flex: none; }
  .band-bark {
    position: absolute;
    left: 0;
    bottom: 0;
    width: 760px;
    height: 22px;
    background: var(--bark);
  }
  .band-orange {
    position: absolute;
    right: 0;
    bottom: 34px;
    width: 270px;
    height: 18px;
    background: var(--orange);
  }
</style>
</head>
<body>
  <section class="card">
    <div class="tree-illustration" role="img" aria-label="Whimsical tree with a curling brown trunk and a canopy of teal and peach leaves, flowers and swirls"></div>

    <div class="identity">
      <div class="name">Meg Donlan</div>
      <div class="role">Facilitator</div>
    </div>

    <h1 class="business-name">Riverbend Circle Gatherings Collective</h1>

    <ul class="contact">
      <li>
        <svg viewBox="0 0 24 24" aria-hidden="true">
          <circle cx="12" cy="12" r="12" fill="var(--orange)"/>
          <path d="M7 9c0-1 1-2 2-2h6c1 0 2 1 2 2v1h-3V9h-4v1H7z M8 11h8l1 6H7z" fill="#fff"/>
        </svg>
        <span>0431 582 917</span>
      </li>
      <li>
        <svg viewBox="0 0 24 24" aria-hidden="true">
          <circle cx="12" cy="12" r="12" fill="var(--orange)"/>
          <rect x="6" y="8" width="12" height="8" fill="#fff"/>
          <path d="M6 8l6 5 6-5" fill="none" stroke="var(--orange)" stroke-width="1.4"/>
        </svg>
        <span>hi.meg.donlan@larkmail.example</span>
      </li>
    </ul>

    <div class="band-bark"></div>
    <div class="band-orange"></div>
  </section>
</body>
</html>
```